Dentistry Office

We want a new design for a Dentist's office website.

The theme is: "We provide high quality, state-of-the-art, dental care in a comfortable, caring environment."

The site currently has a menu on the left of the page with about 40 items on it. There is a great deal of textual content on each page, plus several illustrations.

We want to do this using CSS, so we need specifications in the CSS for all possible elements. The CSS needs to be named in a logical manner for easy use.

Every dentist on the planet seems to use lots of Flash. We don't want to because it is so distracting. We are looking for an elegant solution targeting 24-55 age group, but not excluding anyone.

The following (from another dentist's site) can give you a taste of what we want to communicate on the site:

"After 20 years of teaching dentists how to refine their technique and many years of writing textbooks, I currently devote my time to my office and the hands-on practice of dentistry. I'd like to welcome you personally to my dental practice, and I invite you to meet my highly experienced team of professionals.

"We have offered complete dental care of the highest quality since 1978. We provide Preventive Services, Tooth Whitening and Cosmetic Dentistry for a beautiful smile, Endodontics (root canal treatment) to treat painful teeth, Sedation Dentistry so you can relax, and Dental Implants to restore what is missing. We offer total care.

"Our approach to your health is simple: We use our education, experience and dedication to provide every patient with superior dental care.

"This passion for excellence is not just a goal, but a standard every member of our team holds.

"We also pride ourselves with our state of the art procedures, training and technology. This includes creating a beautiful smile using techniques that preserve as much of the original tooth as possible.

"Our abilities are renowned throughout the dental profession and I hope if you have any questions you will contact us by an e-mail note, by phone or just by dropping by."

Keep in mind the screen shape and dimensions. Your design needs to work in the normal screen proportions, regardless of how it looks when you post it here. Scrolling is OK, but the first impression needs to work.
Updates

Keep in mind that there will be about 250 words, or more, on each page.

Competitors web sites:

http://www.brindlecovedentist.example/

http://www.brindlecovedentalcare.example/

http://www.grinsbymarlowvaledental.example/

http://www.tenbyfamilydentalcare.example/

http://www.quelmardental.example/

http://www.dovrinadental.example/

We need to compete with these.

Target Market(s)

Generally adults seeking the most experienced and comfortable-to-be-with dentist.

Industry/Entity Type

Training

Requirements
Must have
• Must stand apart from other dentists.
• Must be elegant.
• Must have a horizontal menu structure across all columns, NOT a vertical that requires scrolling, no popout, pop down, etc. menus.
• We are looking for something special.
• Do not waste your time or ours putting up templates and things you have used before.
• Personally, I do not see how someone outside the US can understand the northern California dental market. But you are welcome to try.
Should not have
• Flash or graphics that move
• The look of a template
• Folksy fonts
• Looks like you used it 20 times before

```html
<!DOCTYPE html>
<html lang="en">
<head>
<meta charset="utf-8">
<title>Owen Tressler, DDS, FAGD — Brindle Cove Dentist</title>
<link href="https://fonts.googleapis.com/css2?family=Gelasio:ital,wght@0,400;0,700;1,700&family=Arimo:wght@400;700&display=swap" rel="stylesheet">
<style>
:root{
  --page-bg:#c3cbcf;
  --page-bg-dark:#9aa5ab;
  --white:#ffffff;
  --ink:#222222;
  --brand:#1c7fd6;
  --nav:#111111;
  --hero-a:#0b55b8;
  --hero-b:#3f8fe0;
  --hero-c:#9cc8f2;
  --menu-bg:#d9e9f8;
  --menu-line:#9fbfe0;
  --box-line:#8c9aa3;
}
*{box-sizing:border-box;margin:0;padding:0}
html,body{width:852px;height:1200px;overflow:hidden}
body{background:linear-gradient(180deg,var(--page-bg) 0%,#d3d9dc 60%,var(--page-bg-dark) 100%);font-family:"Arimo",Arial,sans-serif;color:var(--ink);position:relative}
.site{position:absolute;left:36px;top:0;width:777px;height:1200px}

/* header */
.site-header{position:absolute;left:0;top:0;width:777px;height:73px;background:linear-gradient(180deg,#ffffff,#eef0f1)}
.brand{position:absolute;left:27px;top:20px;font-family:"Gelasio",Georgia,serif;font-size:22px;color:var(--ink);line-height:1}
.brand .cred{color:var(--brand)}
.brand-tag{position:absolute;left:156px;top:45px;font-family:"Gelasio",Georgia,serif;font-size:11px;color:var(--ink)}
.header-address{position:absolute;left:654px;top:16px;font-family:"Gelasio",Georgia,serif;font-size:9px;line-height:12px;color:var(--ink);font-style:normal}

/* nav */
.main-nav{position:absolute;left:0;top:73px;width:777px;height:30px;background:linear-gradient(180deg,#2a2a2a,var(--nav));display:flex;align-items:center;justify-content:space-between;padding:0 34px 0 46px}
.main-nav a{color:var(--white);text-decoration:none;font-family:"Gelasio",Georgia,serif;font-weight:700;font-size:10px;white-space:nowrap}
.main-nav .sep{color:var(--white);font-size:10px}

/* hero */
.hero{position:absolute;left:0;top:107px;width:777px;height:188px;border:3px solid #1763c9;border-radius:3px;background:linear-gradient(100deg,var(--hero-a) 0%,var(--hero-b) 55%,var(--hero-c) 100%);overflow:hidden}
.hero-quote{position:absolute;left:37px;top:52px;width:390px;font-family:"Gelasio",Georgia,serif;font-size:15.5px;line-height:21px;color:var(--white)}
.hero-mark{position:absolute;font-family:"Gelasio",Georgia,serif;font-size:26px;color:#bcd8f5;line-height:1}
.hero-photo{position:absolute;right:0;top:0;width:230px;height:182px;background:linear-gradient(90deg,rgba(156,200,242,0) 0%,#e9d9cf 35%,#f3e6dc 70%,#f6c7d6 100%)}

/* topic menu */
.topic-menu{position:absolute;left:0;top:307px;width:777px;height:153px;background:var(--menu-bg);border-radius:4px 4px 0 0}
.topic-col{position:absolute;top:8px}
.topic-col h3{font-family:"Gelasio",Georgia,serif;font-weight:400;font-size:12.5px;color:var(--ink);border-bottom:1px solid var(--menu-line);padding-bottom:2px;margin-bottom:3px;width:112px}
.topic-col ul{list-style:none}
.topic-col li{font-size:8.6px;line-height:12px;color:var(--ink);padding-left:9px;position:relative;white-space:nowrap}
.topic-col li::before{content:"";position:absolute;left:1px;top:4px;border-left:4px solid var(--brand);border-top:2.5px solid transparent;border-bottom:2.5px solid transparent}

/* content */
.content{position:absolute;left:0;top:460px;width:777px;height:607px;background:var(--white)}
.main-copy{position:absolute;left:27px;top:16px;width:530px;font-size:8.6px;line-height:11.6px;color:var(--ink)}
.main-copy h1{font-family:"Gelasio",Georgia,serif;font-weight:400;font-size:16.5px;color:var(--brand);margin-bottom:10px}
.main-copy h2{font-family:"Gelasio",Georgia,serif;font-weight:400;font-size:12px;color:var(--ink);margin:12px 0 7px}
.main-copy p{margin-bottom:9px}
.services{list-style:none;margin-bottom:6px}
.services li{position:relative;padding-left:11px;margin-bottom:7px}
.services li::before{content:"";position:absolute;left:1px;top:2px;border-left:4px solid var(--brand);border-top:2.5px solid transparent;border-bottom:2.5px solid transparent}
.main-copy .approach{font-family:"Gelasio",Georgia,serif;font-size:11.6px;line-height:15px;color:var(--brand);margin:16px 0 22px}
.sign-name{font-size:11.5px;color:var(--brand)}

.sidebar{position:absolute;left:575px;top:36px;width:167px}
.office-photo{width:167px;height:122px;border:1px solid var(--box-line);border-radius:8px;padding:4px;background:var(--white)}
.office-photo div{width:100%;height:100%;border-radius:5px;background:linear-gradient(160deg,#3d5a3a 0%,#7b6a55 45%,#a89b86 70%,#2f4a2c 100%)}
.side-box{border:1px solid var(--box-line);border-radius:8px;background:var(--white);margin-top:26px;text-align:center;box-shadow:0 1px 2px rgba(0,0,0,.1)}
.side-box h4{font-family:"Gelasio",Georgia,serif;font-weight:400;font-size:12.5px;color:var(--ink);padding-top:5px}
.map-area{width:150px;height:214px;margin:6px auto 4px;background:linear-gradient(180deg,#f4f4f4,#e6e9ec);border:1px solid #d0d4d7}
.map-link{font-size:8px;text-decoration:underline;color:var(--ink);display:block;padding-bottom:8px}
.hours{text-align:left;padding:4px 14px 10px;font-size:8.6px;line-height:13px;margin-top:12px}
.hours h4{text-align:center;padding-top:2px;margin-bottom:4px}
.hours ul{list-style:none;margin-top:3px}
.hours li{position:relative;padding-left:9px;font-weight:700;font-style:italic}
.hours li::before{content:"";position:absolute;left:0;top:4px;border-left:4px solid var(--brand);border-top:2.5px solid transparent;border-bottom:2.5px solid transparent}

/* footer */
.site-footer{position:absolute;left:0;top:1067px;width:777px;height:133px}
.footer-info{position:absolute;left:0;top:30px;font-size:8.6px;line-height:11px;color:var(--ink)}
.footer-info p{margin-bottom:10px}
.dental-links{position:absolute;left:441px;top:20px;width:333px;height:106px;border:2px solid #5b6166;border-radius:8px;background:#dfe3e5}
.dental-links h5{font-weight:400;font-size:8px;position:absolute;left:10px;top:4px}
.link-col{position:absolute;top:18px}
.badge{height:26px;margin-bottom:4px}
.badge-a{width:48px;background:#1a8a45}
.badge-b{width:64px;background:#9aa0a4;border-radius:13px}
.badge-c{width:26px;background:#5b7f86}
.link-col ul{list-style:none;font-size:7.2px;line-height:8.4px;color:var(--ink)}
</style>
</head>
<body>
<div class="site">

  <header class="site-header">
    <div class="brand">Owen Tressler, <span class="cred">DDS, FAGD</span></div>
    <div class="brand-tag">Brindle Cove Dentist</div>
    <address class="header-address">
      Owen Tressler, DDS, FAGD<br>2200 Linden Ave. Ste E<br>Brindle Cove, CA 90000<br>555-014-2290
    </address>
  </header>

  <nav class="main-nav">
    <a href="#">Home</a><span class="sep">|</span>
    <a href="#">Why We Are Different?</a><span class="sep">|</span>
    <a href="#">Technologies We Offer</a><span class="sep">|</span>
    <a href="#">Meet Dr. Tressler</a><span class="sep">|</span>
    <a href="#">Our Staff</a><span class="sep">|</span>
    <a href="#">Contact Us / Links</a>
  </nav>

  <section class="hero">
    <span class="hero-mark" style="left:27px;top:32px">&ldquo;</span>
    <p class="hero-quote">Brindle Cove Dentist - Owen Tressler, DDS, Providing Cosmetic Dentistry Excellence to Patients in Brindle Cove, Calder County and the Marrow Bay Area.</p>
    <span class="hero-mark" style="left:392px;top:134px">&rdquo;</span>
    <div class="hero-photo" role="img" aria-label="Smiling patient holding a pink flower"></div>
  </section>

  <section class="topic-menu">
    <div class="topic-col" style="left:27px">
      <h3>Education</h3>
      <ul><li>Emergency Dental Care</li><li>Your Mouth</li><li>Your Tooth</li><li>Cracked Tooth?</li><li>Missing a Tooth?</li><li>Sensitive Teeth</li><li>Dry Mouth</li><li>Tooth Grinding</li><li>Sleep Dentistry</li><li>Videos</li></ul>
    </div>
    <div class="topic-col" style="left:175px">
      <h3>Preventative</h3>
      <ul><li>What is Preventive Care?</li><li>Taking Care of Your Teeth</li><li>Eating Right</li><li>Dental Check-Ups</li><li>Sealants</li><li>Periodontal Disease</li><li>Kicking the Habit</li><li>Night Guards</li><li>Dental X-Rays</li><li>Antibiotics with Treatment</li></ul>
    </div>
    <div class="topic-col" style="left:344px">
      <h3>Cosmetics</h3>
      <ul><li>Cosmetic Dentistry</li><li>Bleaching and Whitening</li><li>Cosmetic Bonding</li><li>Esthetic Veneers</li><li>Tooth Shaping</li></ul>
    </div>
    <div class="topic-col" style="left:509px">
      <h3>Restorations</h3>
      <ul><li>Crowns/Caps: Each Step</li><li>CMBRs</li><li>Porcelain Bridges</li><li>Bonded Dental Bridges</li><li>Gold Restorations</li><li>Implants</li><li>Treating Cracked Teeth</li><li>Periodontal (gum) Treatment</li></ul>
    </div>
    <div class="topic-col" style="left:653px">
      <h3>Visiting our office</h3>
      <ul><li>Where to Stay</li><li>First Visit / Map</li><li>Financial Policy</li><li>Dental Insurance</li></ul>
    </div>
  </section>

  <main class="content">
    <article class="main-copy">
      <h1>Welcome to Our Website</h1>
      <p>In Brindle Cove, when you're a patient of Dr. Tressler, you can be confident that you're receiving care from the most experienced, knowledgeable, and skilled cosmetic dentist in Calder County.</p>
      <p>Dr. Tressler is an award-winning leader in restorative dentistry and a genial professional. His humor, dedication, and talent ensure you a pleasant experience and superb, long-lasting results.</p>
      <h2>Dr. Tressler Provides</h2>
      <ul class="services">
        <li>General dentistry—oral hygiene, cavity detection and repair, crowns.</li>
        <li>Cosmetic/restorative dentistry—broken or misshapen teeth, crooked smiles, unsightly gaps</li>
        <li>Non-metal fillings—nontoxic, durable tooth-colored resin fillings that are proven to provide better results</li>
        <li>Tooth shaping—extending, shortening or otherwise reshaping teeth for improved esthetics</li>
        <li>Complete smile make-over's—resin veneers that reshape the whole mouth while preserving natural teeth</li>
        <li>Tooth whitening—at-home bleaching options to make teeth appear years younger</li>
        <li>Laser Dentistry, Sleep Dentistry, and Implant Dentistry with the Finest and Latest Equipment and Materials.</li>
        <li>Dental Implants to replace missing teeth.</li>
        <li>Sedation Dentistry so you can be relaxed.</li>
      </ul>
      <h2>Dr. Tressler's Commitment</h2>
      <p>After 25 years of teaching dentists how to refine their technique and many years of writing textbooks, I currently devote my time to my office and the hands-on practice of dentistry. I'd like to welcome you personally to my dental practice, and I invite you to meet my highly experienced team of professionals.</p>
      <p>Dr. Tressler and his Associates have offered complete dental care of the highest quality since 1978. We provide Preventive Services, Tooth Whitening and Cosmetic Dentistry for a beautiful smile, Endodontics (root canal treatment) to treat painful teeth, Sedation Dentistry so you can relax, and Dental Implants to restore what is missing. We offer total care.</p>
      <p class="approach">Our approach to your health is simple: We use our education, experience and dedication to provide every patient with superior dental care.<br><br>This passion for excellence is not just a goal, but a standard every member of our team holds.</p>
      <p>We also pride ourselves with our state of the art procedures, training and technology. This includes creating a beautiful smile using techniques that preserve as much of the original tooth as possible.</p>
      <p>Our abilities are renowned throughout the dental profession and I hope if you have any questions you will contact us by an e-mail note, by phone or just by dropping by.</p>
      <p>Thank you.</p>
      <p>Sincerely,</p>
      <p class="sign-name">Owen Tressler, DDS FAGD</p>
    </article>

    <aside class="sidebar">
      <div class="office-photo"><div role="img" aria-label="Dental office building surrounded by trees"></div></div>
      <div class="side-box">
        <h4>Brindle Cove Map:</h4>
        <div class="map-area" role="img" aria-label="Street map showing the route to the office"></div>
        <a class="map-link" href="#">Click for Large View</a>
      </div>
      <div class="side-box hours">
        <h4>Office Timing</h4>
        Our usual office hours are:
        <ul><li>Monday 9 am to 6 pm</li><li>Tuesday 9 am to 5 pm</li><li>Wednesday 9 am to 5 pm</li><li>Thursday 9 am to 5 pm</li><li>Friday 7:30 am to 5 pm</li></ul>
      </div>
    </aside>
  </main>

  <footer class="site-footer">
    <div class="footer-info">
      <p>Copyright © 2010 tresslerdental.example. All Rights Reserved.</p>
      <p>Office Phone: (555) 014-2290<br>Office Fax: (555) 014-7733<br>email Dr. Tressler at: drtressler@tresslerdental.example</p>
    </div>
    <div class="dental-links">
      <h5>Dental Links:</h5>
      <div class="link-col" style="left:10px">
        <div class="badge badge-a"></div>
        <ul><li>Emergency Dental Help</li><li>Oral Health Videos</li><li>Oral Health Topics</li><li>Dental Minute News</li></ul>
      </div>
      <div class="link-col" style="left:104px">
        <div class="badge badge-b"></div>
        <ul><li>Dental Emergencies</li><li>Dental Health</li><li>Dental Insurance</li><li>Kids Corner</li><li>Dental Terminology</li></ul>
      </div>
      <div class="link-col" style="left:200px">
        <div class="badge badge-c"></div>
        <ul><li>Course Outlines</li><li>Upcoming Courses</li><li>Web Links</li><li>Dr Tressler CV</li><li>Mentor Store</li></ul>
      </div>
    </div>
  </footer>

</div>
</body>
</html>
```